Verdant Systems Business Card

want the back of card to be blue- with the logo in the center
front of card- info plus logo (info being mailing address, email address, and website address )
4 different names with titles to have on cards
1) Calvin Borsted - Owner
2) Naomi Trelvik- Customer Relationship Specialist
3) Felix Andrade- Vice President of Sales
4) Owen Markby- Chief Technology Officer

Target Market(s)

tech company in the government/probation office industry

Industry/Entity Type

Government Office

Contact Information for Business Card

1) Calvin Borsted - Owner

Colors
0355a3
ffffff

Requirements
Must have
• back side should be blue, with the logo placed in the center
• front side needs to include both the logo, as well as company info (info should include website address, email address, and mailing address)

```html
<!DOCTYPE html>
<html lang="en">
<head>
<meta charset="utf-8">
<title>Verdant Systems Business Card</title>
<link href="https://fonts.googleapis.com/css2?family=Crimson+Text:wght@600&family=Roboto:wght@400&display=swap" rel="stylesheet">
<style>
  :root {
    --navy: #172a52;
    --ink: #1b2d57;
    --text-grey: #555a60;
    --muted-grey: #8a8d91;
    --faint: #e9ebef;
    --paper: #ffffff;
    --backdrop: #ececea;
  }
  * { margin: 0; padding: 0; box-sizing: border-box; }
  html, body {
    width: 1125px; height: 1200px; overflow: hidden;
    background: var(--backdrop);
  }
  .canvas { position: relative; width: 1125px; height: 1200px; }
  .card {
    position: absolute; left: 171px; width: 826px; height: 471px;
    overflow: hidden;
    box-shadow: 0 3px 8px rgba(0,0,0,0.18);
  }
  .card--front { top: 106px; background: var(--paper); }
  .card--back { top: 639px; background: var(--navy); }

  .brand {
    position: absolute; display: flex; align-items: center; gap: 14px;
    font-family: "Crimson Text", Georgia, serif; font-weight: 600;
    letter-spacing: 0.5px; white-space: nowrap;
  }
  .brand__mark { width: 22px; height: 22px; background: currentColor; }
  .card--front .brand { left: 66px; top: 110px; font-size: 50px; color: var(--ink); }
  .card--back .brand {
    left: 50%; top: 180px; transform: translateX(-50%);
    font-size: 56px; color: var(--paper);
  }

  .backdrop-shape {
    position: absolute; left: 440px; top: 150px;
    width: 460px; height: 460px; border-radius: 50%;
    border: 26px solid var(--faint);
  }

  .contact { position: absolute; left: 60px; top: 312px; list-style: none; }
  .contact li {
    display: flex; align-items: center; gap: 13px; height: 26px;
    font-family: "Roboto", Arial, sans-serif; font-size: 19px; color: var(--text-grey);
  }
  .contact svg { width: 16px; height: 16px; fill: var(--ink); flex: none; }

  .person { position: absolute; right: 92px; top: 322px; text-align: right; }
  .person__name {
    font-family: "Crimson Text", Georgia, serif; font-weight: 600;
    font-size: 35px; color: var(--ink); line-height: 1.1;
  }
  .person__title {
    font-family: "Roboto", Arial, sans-serif; font-size: 20px;
    color: var(--muted-grey); margin-top: 2px;
  }

  .back-url {
    position: absolute; left: 0; right: 0; top: 372px; text-align: center;
    font-family: "Roboto", Arial, sans-serif; font-size: 19px;
    letter-spacing: 3.4px; color: var(--paper);
  }
</style>
</head>
<body>
<div class="canvas">
  <section class="card card--front">
    <div class="backdrop-shape"></div>
    <div class="brand"><span class="brand__mark"></span>Verdant Systems</div>
    <ul class="contact">
      <li>
        <svg viewBox="0 0 16 16"><path d="M3.6 1.2 6 3.6 4.7 5.7c.9 2.1 3.5 4.7 5.6 5.6l2.1-1.3 2.4 2.4-1.6 2.2C8.2 14.3 1.7 7.8 1.4 2.8z"/></svg>
        555-218-4079
      </li>
      <li>
        <svg viewBox="0 0 16 16"><path d="M4.5 0h7A1.5 1.5 0 0 1 13 1.5v13a1.5 1.5 0 0 1-1.5 1.5h-7A1.5 1.5 0 0 1 3 14.5v-13A1.5 1.5 0 0 1 4.5 0zm.3 2v10.5h6.4V2zM8 13.4a.9.9 0 1 0 0 1.8.9.9 0 0 0 0-1.8z"/></svg>
        555-730-6152
      </li>
      <li>
        <svg viewBox="0 0 16 16"><path d="M0 3h16v10H0zm1.8 1.5v.3L8 9l6.2-4.2v-.3zm0 2.1v5h12.4v-5L8 10.8z"/></svg>
        info@verdantsystems.com
      </li>
      <li>
        <svg viewBox="0 0 16 16"><path d="M8 0a8 8 0 1 0 0 16A8 8 0 0 0 8 0zM3 4.5l2 .5 1 2-1 1.5.5 2.5-2-1-1-3zm6-2.5 2 1-1 2-2 .5-1-1.5zm3 9-2 2-1-2 1-2 2.5 0z"/></svg>
        www.verdantsystems.com
      </li>
    </ul>
    <div class="person">
      <p class="person__name">Calvin Borsted</p>
      <p class="person__title">Owner</p>
    </div>
  </section>

  <section class="card card--back">
    <div class="brand"><span class="brand__mark"></span>Verdant Systems</div>
    <p class="back-url">www.verdantsystems.com</p>
  </section>
</div>
</body>
</html>
```